Fitness Equipment Repair Business Needs a Catchy New Business Card

We have an existing business card, however, it is quite plain and boring. We are expanding primarily in the commercial area (gyms, studios, apartment complexes etc). The business card will serve as eye candy to those managers/owners that can't be met for a face to face.
Originally I was planning for a brochure as well, but all of our information is better summarized on our website. (brightloopservice.ca).
I would like the card to match the colour scheme of the website and utilize the logo. It should have a professional clean feel to it, however, a little colouring outside the lines wouldn't hurt.
The example card is for my service technician (Colin Marsh). If possible I would like to be able to edit the text to use for more than one person.

Industry/Entity Type

Appliance Repair

Contact Information for Business Card

Clean, crisp and professional but needs to be eye catching. Preferably using the black, white and red colour scheme matching the website. Double sided would be nice, but is not necessary.

Colors
ec1f27
ffffff
000000

Requirements
Must have
• Must be able to edit name, phone number and title to use for multiple people. Must show the company website (brightloopservice.ca).

```html
<!DOCTYPE html>
<html lang="en">
<head>
<meta charset="utf-8">
<title>Brightloop Service – Business Card</title>
<link rel="stylesheet" href="https://fonts.googleapis.com/css2?family=Arvo:wght@400;700&family=Cinzel:wght@700&display=swap">
<style>
  :root {
    --red: #ec1f27;
    --white: #ffffff;
    --black: #000000;
    --stage: #222222;
    --ink: #111111;
  }
  * { box-sizing: border-box; margin: 0; padding: 0; }
  html, body { width: 1189px; height: 1200px; overflow: hidden; background: var(--stage); }
  .canvas { position: relative; width: 1189px; height: 1200px; }

  .card {
    position: absolute; left: 171px; width: 856px; height: 489px;
    background: var(--white); overflow: hidden;
    box-shadow: 0 2px 6px rgba(0,0,0,.5);
  }
  .card--front { top: 66px; }
  .card--back { top: 625px; }

  .illustration { position: absolute; }
  .card--front .illustration {
    left: 314px; top: 52px; width: 224px; height: 300px;
    background: linear-gradient(180deg, #f3f3f3 0%, #dcdcdc 100%);
    border-radius: 6px;
  }
  .wordmark {
    position: absolute; left: 0; right: 0; text-align: center;
    font-family: "Cinzel", serif; font-weight: 700; letter-spacing: 1px;
  }
  .card--front .wordmark { top: 388px; font-size: 36px; color: var(--black); }

  .back-panel {
    position: absolute; left: 0; top: 0; width: 419px; height: 100%;
    background: var(--black);
  }
  .back-panel .illustration {
    left: 114px; top: 73px; width: 220px; height: 280px;
    background: linear-gradient(180deg, #2a2a2a 0%, #151515 100%);
    border-radius: 6px;
  }
  .back-panel .wordmark { top: 368px; font-size: 32px; color: var(--white); }
  .accent-bar {
    position: absolute; left: 419px; top: 0; width: 8px; height: 100%;
    background: var(--red);
  }

  .contact {
    position: absolute; left: 488px; top: 94px;
    font-family: "Arvo", serif; color: var(--ink);
  }
  .contact__name { font-size: 29px; font-weight: 700; line-height: 1; letter-spacing: -0.3px; }
  .contact__title { font-size: 20px; color: var(--red); line-height: 1.2; margin-top: 2px; }
  .contact__address { font-size: 20px; line-height: 29px; margin-top: 26px; }
  .contact__list { list-style: none; margin-top: 24px; font-size: 20px; }
  .contact__list li { display: flex; align-items: center; height: 31px; }
  .contact__list svg { width: 22px; height: 20px; margin-right: 16px; fill: var(--red); }
  .contact__web { font-size: 20px; margin-top: 13px; }
  .contact__web span { color: var(--red); }
</style>
</head>
<body>
<main class="canvas">

  <section class="card card--front">
    <div class="illustration" role="img" aria-label="Line drawing of a muscular technician in a hard hat holding a wrench"></div>
    <h1 class="wordmark">Brightloop Service</h1>
  </section>

  <section class="card card--back">
    <div class="back-panel">
      <div class="illustration" role="img" aria-label="White line drawing of a muscular technician in a hard hat holding a wrench"></div>
      <p class="wordmark">Brightloop</p>
    </div>
    <div class="accent-bar"></div>

    <div class="contact">
      <p class="contact__name">Colin Marsh</p>
      <p class="contact__title">service technician</p>
      <p class="contact__address">518 Carver Road NW<br>Edmonton AB T5K 2L9</p>
      <ul class="contact__list">
        <li>
          <svg viewBox="0 0 22 20" aria-hidden="true"><rect x="6" y="0" width="10" height="20" rx="2"/><rect x="8" y="3" width="6" height="6" fill="#fff"/><rect x="8" y="11" width="6" height="6" fill="#fff" opacity=".6"/></svg>
          555-014-2286
        </li>
        <li>
          <svg viewBox="0 0 22 20" aria-hidden="true"><path d="M1 7c0-3 4-5 10-5s10 2 10 5l-4 1-1-2H6L5 8z"/><path d="M5 10h12l2 8H3z"/><circle cx="11" cy="14" r="2" fill="#fff"/></svg>
          555-017-4410
        </li>
        <li>
          <svg viewBox="0 0 22 20" aria-hidden="true"><rect x="0" y="3" width="22" height="15"/><path d="M1 4l10 8 10-8" stroke="#fff" stroke-width="1.6" fill="none"/><path d="M1 17l7-6M21 17l-7-6" stroke="#fff" stroke-width="1.4"/></svg>
          brightloop@mailbox.ca
        </li>
      </ul>
      <p class="contact__web">www.<span>brightloopservice</span>.ca</p>
    </div>
  </section>

</main>
</body>
</html>
```